business card - Helicopter Flight Services, Flight School, etc.

We need a business card design for a new helicopter service.

We offer Helicopter Flight Services, Aerial Filming & Photography, Flight School, and Helicopter Tours. In that order.

Summit BladeAir, Inc.
Dennis Tollerby
SummitBladeair@Kestmail.com
626-418-7352

Based at the Brenwick Airport in Van Nuys, CA. The final design should communicate integrity and safety. Pictures or logos at your discretion.

Card back side - surprise me.

```html
<!DOCTYPE html>
<html lang="en">
<head>
<meta charset="utf-8">
<title>Summit BladeAir, Inc. — Business Card</title>
<link rel="stylesheet" href="https://fonts.googleapis.com/css2?family=Open+Sans:wght@400;600;700&display=swap">
<style>
  :root {
    --backdrop: #ece8e3;
    --card-white: #ffffff;
    --blue-light: #3aa6de;
    --blue-mid: #1c7fd0;
    --blue-deep: #0a4aa6;
    --brand-blue: #1f6fc0;
    --silver: #b9bcc0;
    --text-light: #ffffff;
    --text-soft: #d3e6f7;
  }
  * { box-sizing: border-box; margin: 0; padding: 0; }
  html, body { width: 1200px; height: 913px; overflow: hidden; }
  body {
    background: var(--backdrop);
    font-family: "Open Sans", Arial, sans-serif;
    position: relative;
  }
  .card {
    position: absolute;
    width: 520px;
    height: 300px;
    border-radius: 18px;
    overflow: hidden;
    box-shadow: 0 10px 28px rgba(0,0,0,.18);
  }
  .card--front { left: 70px; top: 110px; background: var(--card-white); }
  .card--back {
    left: 610px; top: 500px;
    background: linear-gradient(160deg, var(--blue-light) 0%, var(--blue-mid) 45%, var(--blue-deep) 100%);
  }
  .front-shape { position: absolute; inset: 0; }

  .brand {
    position: absolute;
    left: 28px; top: 126px;
    display: flex; align-items: center; gap: 10px;
  }
  .brand__mark {
    width: 42px; height: 42px; border-radius: 50%;
    background: var(--silver);
    border: 2px solid var(--brand-blue);
    flex: none;
  }
  .brand__name {
    font-weight: 700;
    font-size: 16px;
    line-height: 1.2;
    letter-spacing: .4px;
    color: var(--brand-blue);
    text-transform: uppercase;
    white-space: nowrap;
  }

  .contact {
    position: absolute;
    right: 24px; top: 32px;
    text-align: right;
    color: var(--text-light);
  }
  .contact__name { font-weight: 700; font-size: 19px; line-height: 1.25; }
  .contact__role { font-size: 11px; color: var(--text-soft); }
  .contact__line {
    display: flex; justify-content: flex-end; align-items: center; gap: 6px;
    font-size: 12px; margin-top: 9px; white-space: nowrap;
  }
  .contact__line + .contact__line { margin-top: 3px; }
  .contact__line svg { width: 11px; height: 11px; flex: none; }

  .back-emblem {
    position: absolute;
    left: 50%; top: 34px;
    transform: translateX(-50%);
    width: 190px; height: 140px;
    border-radius: 50%;
    background: radial-gradient(circle at 40% 35%, #d9dbde, var(--silver) 70%);
    border: 3px solid var(--card-white);
    display: flex; align-items: center; justify-content: center;
  }
  .back-emblem__name {
    font-weight: 700; font-size: 15px; color: var(--brand-blue);
    text-transform: uppercase; letter-spacing: .5px; text-align: center; line-height: 1.25;
  }
  .services {
    position: absolute;
    left: 0; right: 0; top: 196px;
    text-align: center;
    list-style: none;
    color: var(--text-light);
    font-size: 15px;
    line-height: 1.4;
  }
</style>
</head>
<body>
  <section class="card card--front" aria-label="Card front">
    <svg class="front-shape" viewBox="0 0 520 300" aria-hidden="true">
      <defs>
        <linearGradient id="frontBlue" x1="0" y1="0" x2="0.4" y2="1">
          <stop offset="0" stop-color="#3aa6de"/>
          <stop offset=".5" stop-color="#1c7fd0"/>
          <stop offset="1" stop-color="#0a4aa6"/>
        </linearGradient>
      </defs>
      <path d="M160 0 H520 V300 H285 C335 220 315 80 160 0 Z" fill="url(#frontBlue)"/>
      <path d="M160 0 C315 80 335 220 285 300" fill="none" stroke="#b9bcc0" stroke-width="4"/>
    </svg>

    <div class="brand">
      <span class="brand__mark"></span>
      <span class="brand__name">Summit<br>BladeAir, Inc.</span>
    </div>

    <div class="contact">
      <div class="contact__name">Dennis Tollerby</div>
      <div class="contact__role">Owner</div>
      <div class="contact__line">
        <span>626-418-7352</span>
        <svg viewBox="0 0 24 24"><path d="M6.6 10.8a15.1 15.1 0 0 0 6.6 6.6l2.2-2.2a1 1 0 0 1 1-.25 11.4 11.4 0 0 0 3.6.57 1 1 0 0 1 1 1V20a1 1 0 0 1-1 1A17 17 0 0 1 3 4a1 1 0 0 1 1-1h3.5a1 1 0 0 1 1 1c0 1.25.2 2.45.57 3.57a1 1 0 0 1-.25 1Z" fill="#d3e6f7"/></svg>
      </div>
      <div class="contact__line">
        <span>SummitBladeair@Kestmail.com</span>
        <svg viewBox="0 0 24 24"><rect x="3" y="5" width="18" height="14" rx="2" fill="none" stroke="#d3e6f7" stroke-width="2"/><path d="M3 7l9 6 9-6" fill="none" stroke="#d3e6f7" stroke-width="2"/></svg>
      </div>
    </div>
  </section>

  <section class="card card--back" aria-label="Card back">
    <div class="back-emblem">
      <span class="back-emblem__name">Summit<br>BladeAir, Inc.</span>
    </div>
    <ul class="services">
      <li>Aerial Filming &amp; Photography</li>
      <li>Flight School</li>
      <li>Helicopter Tours (In that order)</li>
    </ul>
  </section>
</body>
</html>
```